RWT Fittings Ltd Business Cards

We need a business card with our business logo. We provide window and door installations on high-rises in west coast British Colombia, Canada.

I would like my business information and details on one side of the card, and the other side the company name with logo

Target Market(s)

General Contractors

Industry/Entity Type

Construction

Contact Information for Business Card

one side i want my company name and logo in the dark theme logo that i provided

Requirements
Must have
• Marco Peltieri, 16045518293, RWTFittings@mailbox-demo.com, 1407-5194 Linden Row Burnaby BC, V5H 2K9, Owner & Manager

```html
<!DOCTYPE html>
<html lang="en">
<head>
<meta charset="utf-8">
<title>RWT Fittings Ltd Business Cards</title>
<link rel="stylesheet" href="https://fonts.googleapis.com/css2?family=Montserrat:wght@700&family=Roboto:wght@400;500;700&display=swap">
<style>
  :root {
    --page: #2a2a2e;
    --card: #1f1f23;
    --blue: #29a9e1;
    --white: #f2f2f2;
    --grey: #a8a8ad;
    --text-font: "Roboto", Arial, sans-serif;
    --name-font: "Montserrat", Arial, sans-serif;
  }
  * { box-sizing: border-box; margin: 0; padding: 0; }
  html, body { width: 1200px; height: 780px; overflow: hidden; }
  body {
    background: var(--page);
    display: flex;
    align-items: center;
    justify-content: center;
    gap: 40px;
    font-family: var(--text-font);
  }
  .card {
    position: relative;
    width: 540px;
    height: 310px;
    background: var(--card);
    border-radius: 26px;
    border: 2px solid var(--blue);
    border-top-color: var(--card);
    overflow: hidden;
    box-shadow: 0 18px 40px rgba(0,0,0,0.45);
  }
  /* Front: company name only */
  .card--front { display: flex; align-items: center; justify-content: center; }
  .brand { display: flex; align-items: center; gap: 14px; }
  .brand__mark { width: 34px; height: 34px; background: var(--blue); }
  .brand__name {
    font-family: var(--text-font);
    font-weight: 700;
    color: var(--grey);
    font-size: 40px;
    letter-spacing: 0.5px;
  }
  /* Back: details */
  .accent-tab {
    position: absolute; top: 0; right: 70px;
    width: 16px; height: 44px; background: var(--blue);
  }
  .person {
    position: absolute; top: 46px; right: 96px; text-align: right;
  }
  .person__name {
    font-family: var(--name-font);
    font-weight: 700; font-size: 26px; color: var(--blue);
  }
  .person__role {
    font-weight: 500; font-size: 14px; color: var(--white); margin-top: 2px;
  }
  .card--back .brand { position: absolute; left: 38px; top: 128px; gap: 10px; }
  .card--back .brand__mark { width: 26px; height: 26px; background: var(--grey); }
  .card--back .brand__name { font-size: 30px; color: var(--blue); }
  .contact {
    position: absolute; left: 40px; bottom: 30px;
    color: var(--white); font-size: 14px; line-height: 1.45;
  }
  .contact__address { margin-bottom: 10px; }
  .contact__line { display: flex; align-items: center; gap: 8px; }
  .contact__icon { width: 14px; height: 14px; flex: none; }
</style>
</head>
<body>
  <section class="card card--front">
    <div class="brand">
      <span class="brand__mark"></span>
      <span class="brand__name">RWT Fittings Ltd</span>
    </div>
  </section>

  <section class="card card--back">
    <span class="accent-tab"></span>
    <div class="person">
      <p class="person__name">Marco Peltieri</p>
      <p class="person__role">Owner &amp; Manager</p>
    </div>
    <div class="brand">
      <span class="brand__mark"></span>
      <span class="brand__name">RWT Fittings Ltd</span>
    </div>
    <div class="contact">
      <p class="contact__address">1407-5194 Linden Row<br>Burnaby BC, V5H 2K9</p>
      <p class="contact__line">
        <svg class="contact__icon" viewBox="0 0 24 24" aria-hidden="true"><path fill="#29a9e1" d="M6.6 10.8a15.1 15.1 0 0 0 6.6 6.6l2.2-2.2a1 1 0 0 1 1-.25 11.4 11.4 0 0 0 3.6.57 1 1 0 0 1 1 1V20a1 1 0 0 1-1 1A17 17 0 0 1 3 4a1 1 0 0 1 1-1h3.5a1 1 0 0 1 1 1c0 1.25.2 2.45.57 3.57a1 1 0 0 1-.25 1z"/></svg>
        1604 551 8293
      </p>
      <p class="contact__line">
        <svg class="contact__icon" viewBox="0 0 24 24" aria-hidden="true"><rect x="2" y="5" width="20" height="14" rx="2" fill="none" stroke="#29a9e1" stroke-width="2"/><path d="M3 6l9 7 9-7" fill="none" stroke="#29a9e1" stroke-width="2"/></svg>
        RWTFittings@mailbox-demo.com
      </p>
    </div>
  </section>
</body>
</html>
```